www.youthquill.com Creative Website Re-design

We are looking for multiple page designs for a client website (www.youthquill.com). The primary demographic is high school teenagers preparing for college applications. We believe the demographic is slightly skewed to female. We're looking for Home page, Content type main page (for example "All Fiction" http://www.youthquill.com/poetry/ main page would include filters to show Top Pages, Most discussed, newest etc.) User page that a content contributor could log in to see all their content, add content etc. (samples in mock ups loaded). finally an inner page for everything else.
Need to ensure there are applicable advertising spaces as per the current site.
We are looking for a fun teenage friendly design that is bright and cheerful.
Reason: I'm not happy with the quality of the submissions to date or the lack of submissions received. I'm hoping by extending the deadline I can find something that is workable.
Target Market(s)
high school students - primarily female - applying for college
Industry/Entity Type
Education
Number of Pages Required
4 page
Requirements
Must have
- fresh cheerful look - we need to include the ad banners & right side column similar to the current site. The sample mock up is missing those
Nice to have
- logo can be punched up

```html
<!DOCTYPE html>
<html lang="en">
<head>
<meta charset="utf-8">
<title>Youth Quill – Home</title>
<link href="https://fonts.googleapis.com/css2?family=Poppins:wght@300;400;500;600;700&display=swap" rel="stylesheet">
<style>
:root{
  --purple:#3d2f9e;
  --purple-head:#4b3aa6;
  --navy:#1c1a5e;
  --yellow:#f7d21e;
  --ink:#222;
  --muted:#777;
  --light:#f3f3f3;
  --line:#ddd;
}
*{box-sizing:border-box;margin:0;padding:0}
html,body{width:1200px;height:4167px;overflow:hidden;background:#fff;font-family:'Poppins',sans-serif;color:var(--ink)}
.page{position:relative;width:1200px;height:4167px}
.abs{position:absolute}
.ph{position:absolute}
.brand{font-family:'Poppins',sans-serif;font-weight:700;color:var(--yellow);font-size:30px;letter-spacing:-.5px}
/* header */
.search{left:258px;top:22px;width:207px;height:26px;border:1px solid #bbb;font-size:9px;color:#666;padding:6px 8px}
.search svg{position:absolute;right:6px;top:6px}
.tagline{left:258px;top:107px;font-size:7px;color:#888}
.promo{left:480px;top:63px;width:455px;height:57px;background:#fff;border:1px solid #eee}
.promo .pct{position:absolute;left:10px;top:4px;font-size:40px;font-weight:700;color:#e0218a;line-height:1}
.promo .off{position:absolute;left:92px;top:10px;font-size:9px;font-weight:700;color:#e0218a}
.promo .txt{position:absolute;left:125px;top:10px;font-size:11px;color:#3aa0d8;font-weight:600;line-height:1.2}
.promo .prod{position:absolute;left:265px;top:8px;width:70px;height:42px;background:linear-gradient(135deg,#c9a27a,#6e8aa8)}
.promo .cta{position:absolute;left:345px;top:20px;font-size:10px;font-weight:600;color:#3a6fb6}
.connect{left:733px;top:31px;font-size:8px;font-weight:600;color:#444}
.connect i{display:inline-block;width:7px;height:7px;border-radius:50%;background:#777;margin-left:5px;vertical-align:middle}
.login{left:865px;top:25px;width:70px;height:20px;background:var(--yellow);font-size:8px;font-weight:700;text-align:center;line-height:20px}
.nav{left:0;top:136px;width:1200px;height:39px;background:var(--purple)}
.nav ul{position:absolute;left:280px;top:0;display:flex;list-style:none;gap:22px;height:39px;align-items:center}
.nav li{font-size:8.5px;font-weight:600;color:#fff;letter-spacing:.3px}
.nav li.on{border-bottom:2px solid var(--yellow);padding-bottom:3px;color:var(--yellow)}
/* hero */
.hero{left:0;top:175px;width:1200px;height:295px;background:linear-gradient(180deg,var(--navy),#231b6b)}
.slide{left:258px;top:208px;width:455px;height:220px;background:linear-gradient(120deg,#8e1a20,#c8202a 55%,#e9c56a)}
.slide h2{position:absolute;left:24px;top:80px;font-size:17px;font-weight:400;color:#fff}
.slide p{position:absolute;left:24px;top:106px;font-size:7px;color:#fde;width:180px}
.slide .btn{position:absolute;left:24px;top:140px;background:var(--yellow);font-size:8px;font-weight:700;padding:6px 14px}
.dots{display:flex;gap:5px}
.dots i{width:5px;height:5px;border-radius:50%;background:#fff;opacity:.6}
.dots i:first-child{opacity:1}
.box{position:absolute;left:713px;width:227px;height:73px;padding:14px 0 0 58px}
.box svg{position:absolute;left:16px;top:20px}
.box b{display:block;font-size:13px;font-weight:500;color:var(--purple)}
.box span{font-size:7px;color:#777}
.box.sub{background:var(--yellow);top:208px}
.box.w1{background:#fff;top:282px;border-bottom:1px solid var(--line)}
.box.w2{background:#fff;top:355px;height:73px}
/* headings */
.h{position:absolute;font-size:30px;font-weight:500;color:var(--purple-head);line-height:1}
.sub-h{position:absolute;font-size:7px;color:#888}
.sub-h em{color:#e8b900;font-style:normal}
.arrows{position:absolute;font-size:14px;color:#bbb;letter-spacing:6px}
/* print */
.cover{left:258px;top:548px;width:162px;height:187px;background:linear-gradient(160deg,#e4402a,#f3c84a 60%,#3e6ab0)}
.label{left:443px;top:548px;width:182px;height:42px;background:var(--purple);color:#fff;font-size:9px;font-weight:600;line-height:42px;padding-left:16px;clip-path:polygon(0 0,90% 0,100% 50%,90% 100%,0 100%)}
.print-t{left:443px;top:598px;font-size:10px;font-weight:500}
.print-t2{left:443px;top:622px;font-size:10px;font-weight:600;color:var(--purple)}
.print-p{left:443px;top:645px;width:225px;font-size:6.5px;color:#777;line-height:1.5}
.ybtn{position:absolute;background:var(--yellow);font-size:7.5px;font-weight:700;text-align:center;color:#222}
.obtn{position:absolute;border:1px solid #bbb;font-size:7px;font-weight:600;text-align:center;line-height:33px;height:35px}
.pdots{left:262px;top:836px;display:flex;gap:8px}
.pdots i{width:6px;height:6px;border-radius:50%;background:#ccc}
.pdots i:first-child{background:var(--purple)}
/* articles */
.art{position:absolute;left:258px;width:452px}
.art .th{position:absolute;left:0;top:0;width:147px;height:90px}
.art h3{position:absolute;left:165px;top:15px;font-size:15px;font-weight:500;color:var(--purple-head)}
.art .by{position:absolute;left:165px;top:38px;font-size:8px;color:#444}
.art .mini{position:absolute;left:165px;top:58px;font-size:6px;color:#888}
.art .mini em{color:var(--purple);font-style:normal}
.art p{position:absolute;left:0;top:108px;width:452px;font-size:7.5px;line-height:1.6;color:#666}
.art .ybtn{left:0;top:170px;width:122px;height:30px;line-height:30px}
/* hot */
.card{position:absolute;width:213px}
.card .im{height:180px;position:relative}
.card .tag{position:absolute;left:8px;top:8px;background:var(--purple);color:#fff;font-size:6.5px;font-weight:600;padding:3px 6px}
.card h4{font-size:9px;font-weight:600;margin-top:12px}
.card .by{font-size:6.5px;color:#888;margin-top:4px}
.card .cm{font-size:7px;color:#666;margin-top:8px}
.tile{position:absolute;width:142px;height:110px}
.contest{position:absolute;width:143px}
.contest .im{height:110px}
.contest h4{font-size:10px;font-weight:600;margin-top:12px}
/* sidebar */
.ad{position:absolute;left:722px;width:213px}
.ad .t{position:absolute;font-weight:700;line-height:1.15}
.feed-h{position:absolute;left:720px;font-size:23px;font-weight:500;color:var(--purple-head)}
.post{position:absolute;left:722px;width:215px}
.post .av{position:absolute;left:0;top:0;width:36px;height:36px}
.post b{position:absolute;left:44px;top:2px;font-size:10px;font-weight:500}
.post b em{color:#3aa0d8;font-style:normal}
.post small{position:absolute;left:44px;top:18px;font-size:6px;color:#999}
.post .pi{position:absolute;left:0;top:50px;width:215px;height:145px}
.post p{position:absolute;left:0;top:205px;font-size:7px;line-height:1.5;color:#555;width:215px}
.pbtn{position:absolute;left:722px;width:150px;height:30px;background:var(--purple);color:#fff;font-size:8px;font-weight:600;text-align:center;line-height:30px}
/* money */
.money{left:265px;top:3140px;width:443px;height:60px;background:#2ea84a;color:#fff}
.money .a{position:absolute;left:14px;top:14px;font-size:12px;line-height:1.1}
.money .b{position:absolute;left:182px;top:16px;font-size:6.5px;line-height:1.4;width:170px;color:#e6ffe9}
.money .c{position:absolute;right:0;top:0;width:70px;height:60px;background:#fff;color:#2ea84a;font-size:10px;font-weight:700;text-align:center;line-height:60px}
/* goodies */
.goodies{left:0;top:3225px;width:1200px;height:490px;background:var(--light)}
.good{position:absolute;width:180px;text-align:center}
.good .im{width:120px;height:140px;margin:0 auto}
.good h4{font-size:14px;font-weight:500;margin-top:22px}
.good p{font-size:6.5px;color:#777;margin-top:10px}
.good .ybtn{position:relative;display:inline-block;width:80px;height:20px;line-height:20px;margin-top:16px;font-size:6.5px}
/* footer */
.fcol{position:absolute;top:3770px}
.fcol h5{font-size:8px;font-weight:600;color:var(--purple-head);margin-bottom:12px}
.fcol li{list-style:none;font-size:6.5px;color:#666;line-height:1.75}
.bottom{left:0;top:4095px;width:1200px;height:72px;border-top:1px solid var(--line)}
.bottom .brand{position:absolute;left:258px;top:22px;font-size:22px}
.bottom .copy{position:absolute;left:388px;top:33px;font-size:7px;color:#666}
.bottom .soc{position:absolute;left:780px;top:33px;font-size:7px;color:#666}
.bottom .soc i{display:inline-block;width:6px;height:6px;border-radius:50%;background:#777;margin-left:5px;vertical-align:middle}
.bottom .up{position:absolute;left:1160px;top:33px;font-size:7px;color:#666}
</style>
</head>
<body>
<div class="page">

  <div class="abs search">SEARCH
    <svg width="10" height="10" viewBox="0 0 10 10"><circle cx="4" cy="4" r="3" fill="none" stroke="#555" stroke-width="1.2"/><line x1="6.3" y1="6.3" x2="9" y2="9" stroke="#555" stroke-width="1.2"/></svg>
  </div>
  <div class="abs brand" style="left:258px;top:68px">Youth Quill</div>
  <div class="abs tagline">YOUR VOICE, YOUR STORIES, YOUR WORDS</div>
  <div class="abs promo">
    <div class="pct">25%</div><div class="off">OFF</div>
    <div class="txt">ALL CANVAS ORDERS<br>PLUS FREE SHIPPING</div>
    <div class="prod" role="img" aria-label="Canvas print product photo"></div>
    <div class="cta">CANVAS PRINTS</div>
  </div>
  <div class="abs connect">CONNECT WITH US <i></i><i></i><i></i></div>
  <div class="abs login">▸ LOGIN</div>

  <nav class="abs nav"><ul>
    <li class="on">POETRY</li><li>FICTION</li><li>NONFICTION</li><li>REVIEWS</li><li>FORUMS</li><li>ART/PHOTO</li><li>CONTESTS</li><li>SUMMER PROGRAMS</li><li>COLLEGE GUIDE</li>
  </ul></nav>

  <div class="abs hero"></div>
  <div class="abs slide" role="img" aria-label="Gift box with a golden ribbon bow on red">
    <h2>Give Youth Quill as a gift</h2>
    <p>Share a year of stories and art with someone who loves to read.</p>
    <div class="btn">GIFT NOW !</div>
    <div class="dots" style="position:absolute;left:24px;top:195px"><i></i><i></i><i></i><i></i></div>
  </div>
  <div class="box sub">
    <svg width="26" height="20" viewBox="0 0 26 20"><rect x="1" y="1" width="24" height="18" fill="none" stroke="#3d2f9e" stroke-width="1.5"/><polyline points="1,1 13,11 25,1" fill="none" stroke="#3d2f9e" stroke-width="1.5"/></svg>
    <b>Subscribe to Youth Quill</b><span>Get the Print Magazine</span>
  </div>
  <div class="box w1">
    <svg width="24" height="24" viewBox="0 0 24 24"><rect x="2" y="4" width="16" height="18" fill="none" stroke="#555" stroke-width="1.5"/><line x1="10" y1="14" x2="22" y2="2" stroke="#555" stroke-width="1.5"/></svg>
    <b>Submit to Youth Quill</b><span>Click here to share yours</span>
  </div>
  <div class="box w2">
    <svg width="24" height="24" viewBox="0 0 24 24"><circle cx="10" cy="10" r="7" fill="none" stroke="#555" stroke-width="1.6"/><line x1="15" y1="15" x2="22" y2="22" stroke="#555" stroke-width="1.6"/></svg>
    <b>Search Youth Quill</b><span>Articles, Art, Books &amp; Videos</span>
  </div>

  <div class="ph cover" role="img" aria-label="Magazine cover with runners on a track"></div>
  <div class="abs label">MARCH 2017 PRINT ISSUE</div>
  <div class="abs print-t">Subscribe or give a gift »</div>
  <div class="abs print-t2">Youth Quill Magazine March 2017 Edition</div>
  <div class="abs print-p">Whether you're interested in poetry, sports, movie reviews or fiction, there's something inside for you. Find out what other teens across the country are thinking, writing.</div>
  <div class="ybtn" style="left:443px;top:705px;width:157px;height:33px;line-height:33px">FLIP THROUGH CURRENT ISSUE</div>
  <div class="obtn" style="left:262px;top:770px;width:100px">SEE PAST ISSUES</div>
  <div class="obtn" style="left:370px;top:770px;width:100px">SUBSCRIBE NOW</div>
  <div class="obtn" style="left:478px;top:770px;width:166px">VIEW ALL FROM THIS ISSUE</div>
  <div class="abs pdots"><i></i><i></i><i></i><i></i></div>

  <div class="h" style="left:262px;top:888px">Editors Choice</div>
  <div class="sub-h" style="left:264px;top:928px">Teen work hand-picked by our editors. <em>Submit your own »</em></div>
  <div class="arrows" style="left:668px;top:900px">‹ ›</div>

  <div class="art" style="top:995px">
    <div class="th" role="img" aria-label="Black and white photo of a keyboard and notes" style="background:linear-gradient(135deg,#444,#bbb)"></div>
    <h3>Anything Goes</h3><div class="by">By SkyWriterJo, Maple Grove, MN</div><div class="mini"><em>More by this author</em> | 3 Hearts</div>
    <p>The anticipation of the battle thoughts racing through my mind, waiting on my turn to step on the mat to prove dominance over another person. As I listen to music, blocking out the world around me, I'm able to focus on the goal, giving a never say-never option. Losing isn't even a thought.</p>
    <div class="ybtn">READ FULL ARTICLE</div>
  </div>
  <div class="art" style="top:1245px">
    <div class="th" role="img" aria-label="Photo of an elderly man" style="background:linear-gradient(135deg,#9b8a74,#e6dccd)"></div>
    <h3>Grandfather</h3><div class="by">By SkyWriterJo, Maple Grove, MN</div><div class="mini"><em>More by this author</em> | 3 Hearts</div>
    <p>The anticipation of the battle thoughts racing through my mind, waiting on my turn to step on the mat to prove dominance over another person. As I listen to music, blocking out the world around me, I'm able to focus on the goal, giving a never say-never option. Losing isn't even a thought.</p>
    <div class="ybtn">READ FULL ARTICLE</div>
  </div>
  <div class="art" style="top:1495px">
    <div class="th" role="img" aria-label="Photo of a white family house" style="background:linear-gradient(160deg,#7fa3c4,#e8e8e0 60%,#6b8c4a)"></div>
    <h3>Home</h3><div class="by">By SkyWriterJo, Maple Grove, MN</div><div class="mini"><em>More by this author</em> | 3 Hearts</div>
    <p>The anticipation of the battle thoughts racing through my mind, waiting on my turn to step on the mat to prove dominance over another person. As I listen to music, blocking out the world around me, I'm able to focus on the goal, giving a never say-never option. Losing isn't even a thought.</p>
    <div class="ybtn">READ FULL ARTICLE</div>
  </div>

  <div class="h" style="left:262px;top:1777px">What's Hot</div>
  <div class="sub-h" style="left:264px;top:1817px">Today's most popular articles by teens. <em>Submit your own »</em></div>
  <div class="arrows" style="left:668px;top:1795px">‹ ›</div>
  <div class="card" style="left:265px;top:1870px"><div class="im" role="img" aria-label="Book cover with hands holding a red apple" style="background:radial-gradient(circle at 50% 55%,#a01d24 0 14%,#111 40%)"><span class="tag">REVIEW</span></div><h4>Moonfall by Clara Winters</h4><div class="by">By Riley T., Fairview, CA</div><div class="cm">💬 733 comments</div></div>
  <div class="card" style="left:495px;top:1870px"><div class="im" role="img" aria-label="Open book on a sunlit table" style="background:linear-gradient(140deg,#5a4a2a,#c9a564 55%,#3a3020)"><span class="tag">POETRY</span></div><h4>X</h4><div class="by">By Riley T., Fairview, CA</div><div class="cm">💬 733 comments</div></div>
  <div class="card" style="left:265px;top:2145px"><div class="im" role="img" aria-label="Black and white photo of an empty hallway" style="background:linear-gradient(90deg,#222,#ddd 50%,#333)"><span class="tag">FICTION</span></div><h4>A Wish For Her</h4><div class="by">By Riley T., Fairview, CA</div><div class="cm">💬 733 comments</div></div>
  <div class="card" style="left:495px;top:2145px"><div class="im" role="img" aria-label="Group photo of teens with a skateboarder" style="background:linear-gradient(160deg,#6d7b8a,#2d3d5a 60%,#b08a6a)"><span class="tag">NON FICTION</span></div><h4>Skateboarder Dex Rowan</h4><div class="by">By Riley T., Fairview, CA</div><div class="cm">💬 733 comments</div></div>

  <div class="h" style="left:262px;top:2467px">Top Images</div>
  <div class="sub-h" style="left:264px;top:2507px">Voted by you</div>
  <div class="arrows" style="left:668px;top:2485px">‹ ›</div>
  <div class="tile" role="img" aria-label="Pencil drawing of an eye" style="left:265px;top:2560px;background:linear-gradient(135deg,#9aa4ad,#d7dde1)"></div>
  <div class="tile" role="img" aria-label="Graphite portrait sketch" style="left:415px;top:2560px;background:linear-gradient(135deg,#555,#ddd)"></div>
  <div class="tile" role="img" aria-label="Ink drawing of a tree" style="left:565px;top:2560px;background:linear-gradient(135deg,#eee,#888)"></div>
  <div class="tile" role="img" aria-label="Painting of a scarecrow under blue sky" style="left:265px;top:2680px;background:linear-gradient(180deg,#6f8db0,#9a4d3a)"></div>
  <div class="tile" role="img" aria-label="Dark blue toned illustration" style="left:415px;top:2680px;background:linear-gradient(135deg,#2f3a58,#8c95a8)"></div>
  <div class="tile" role="img" aria-label="Sepia photo of a figure in a doorway" style="left:565px;top:2680px;background:linear-gradient(135deg,#5a4a3a,#b8a890)"></div>

  <div class="h" style="left:262px;top:2862px">Contests</div>
  <div class="sub-h" style="left:264px;top:2902px">Voted by you</div>
  <div class="arrows" style="left:668px;top:2880px">‹ ›</div>
  <div class="contest" style="left:265px;top:2950px"><div class="im" role="img" aria-label="Dark magazine cover artwork" style="background:linear-gradient(135deg,#222,#777)"></div><h4>Cover Art Contest</h4></div>
  <div class="contest" style="left:415px;top:2950px"><div class="im" role="img" aria-label="Teacher standing with students" style="background:linear-gradient(135deg,#c8a080,#e6d3b8 50%,#8a6d5a)"></div><h4>Educator of the Year</h4></div>
  <div class="contest" style="left:565px;top:2950px"><div class="im" role="img" aria-label="Golden travel landscape with landmark" style="background:linear-gradient(135deg,#d9b46a,#8d7a50)"></div><h4>Travel &amp; Culture Contest</h4></div>

  <div class="abs money">
    <div class="a">We have answers to<br>your money questions.</div>
    <div class="b">Ask your question and get clear, plain answers from our team of financial experts.</div>
    <div class="c">Moneywise</div>
  </div>

  <div class="ad" style="top:548px;height:177px;background:#1d5fbf">
    <div class="t" style="left:12px;top:12px;font-size:9px;color:#fff">Stackwell</div>
    <div class="t" style="left:12px;top:34px;font-size:16px;color:#fff;width:150px">ITSM software that puts your customers first.</div>
    <div class="t" style="left:12px;top:120px;font-size:6px;font-weight:400;color:#cde">Limited time offer</div>
    <div style="position:absolute;left:12px;top:142px;width:54px;height:16px;background:var(--yellow);font-size:6px;font-weight:700;text-align:center;line-height:16px">Try it free</div>
    <div style="position:absolute;left:140px;top:110px;width:60px;height:55px;background:linear-gradient(135deg,#4fc3e8,#2ea84a)" role="img" aria-label="Illustration of office workers"></div>
  </div>
  <div class="ad" style="top:750px;height:175px;background:linear-gradient(135deg,#e8387a,#f07aa5)">
    <div class="t" style="left:10px;top:12px;font-size:13px;color:var(--yellow)">Kids Game Title</div>
    <div class="t" style="left:10px;top:30px;font-size:6px;color:#fff;font-weight:400">Lorem ipsum dolor sit amet<br>consectetur adipiscing elit</div>
    <div style="position:absolute;left:10px;top:95px;width:38px;height:16px;background:#2ea84a;color:#fff;font-size:6px;font-weight:700;text-align:center;line-height:16px">PLAY NOW</div>
    <div style="position:absolute;left:80px;top:55px;width:52px;height:52px;border-radius:50%;background:var(--yellow);text-align:center;font-size:18px;font-weight:700;line-height:52px;color:var(--purple)">20</div>
    <div style="position:absolute;left:138px;top:40px;width:70px;height:130px;background:linear-gradient(180deg,#f4c27a,#3d6fc4)" role="img" aria-label="Cartoon kid character"></div>
  </div>
  <div class="ad" style="top:950px;height:175px;background:linear-gradient(160deg,#0d2a3a,#14506a)">
    <div class="t" style="left:12px;top:12px;font-size:16px;color:#fff">Vault<br>Cloud<br>Pool</div>
    <div class="t" style="left:90px;top:18px;font-size:6.5px;color:#cfe;font-weight:400;width:110px">Always virtual backups, free to run on demand</div>
    <div style="position:absolute;left:12px;top:100px;width:50px;height:14px;background:#2ea84a;font-size:6px;color:#fff;text-align:center;line-height:14px">Buy Now</div>
    <div style="position:absolute;left:110px;top:80px;width:95px;height:85px;background:linear-gradient(135deg,#2b6f8e,#7fd0e8)" role="img" aria-label="Cloud storage pool illustration"></div>
  </div>

  <div class="feed-h" style="top:1160px">Pagebook Feeds</div>
  <div class="post" style="top:1215px">
    <div class="av" role="img" aria-label="Magazine page avatar" style="background:linear-gradient(135deg,#e4402a,#3e6ab0)"></div>
    <b>Youth Quill Magazine</b><small>23 March at 4:14</small>
    <div class="pi" role="img" aria-label="Photo of a handwritten note" style="background:linear-gradient(135deg,#d8d8d8,#8a8a8a)"></div>
    <p>Game as a Verb: Writers on Choosing to Live Overseas [via Shelfy]</p>
  </div>
  <div class="post" style="top:1493px">
    <div class="av" role="img" aria-label="Magazine page avatar" style="background:linear-gradient(135deg,#e4402a,#3e6ab0)"></div>
    <b>Youth Quill Magazine</b><small>23 March at 4:14</small>
    <div class="pi" role="img" aria-label="Yellow poster with a pair of compasses" style="background:linear-gradient(135deg,#f7e25a,#d9b92a)"></div>
    <p>Game as a Verb: Writers on Choosing to Live Overseas [via Shelfy]</p>
  </div>
  <div class="pbtn" style="top:1768px">VIEW ON PAGEBOOK</div>

  <div class="feed-h" style="top:1832px">Chirper Feeds</div>
  <div class="post" style="top:1885px">
    <div class="av" role="img" aria-label="Magazine account avatar" style="background:linear-gradient(135deg,#e4402a,#3e6ab0)"></div>
    <b>Youth Quill <em>@youthquill</em></b><small>23 March at 4:14</small>
    <p style="top:46px;font-weight:600;color:#333">Why We Love Star-Crossed Love Stories</p>
    <p style="top:62px;color:#999;font-size:6px">http://www.youthquill.com/2017/03/starcrossed-love-stories</p>
    <div class="pi" role="img" aria-label="Silhouette of two people at sunset" style="top:88px;height:150px;background:linear-gradient(180deg,#eee,#444)"></div>
  </div>
  <div class="pbtn" style="top:2183px">VIEW ON CHIRPER</div>

  <div class="abs goodies"></div>
  <div class="h" style="left:0;top:3282px;width:1200px;text-align:center;font-size:30px">Youth Quill Goodies</div>
  <div class="sub-h" style="left:0;top:3325px;width:1200px;text-align:center">You might want to check these out</div>
  <div class="good" style="left:265px;top:3410px"><div class="im" role="img" aria-label="Mint green girls' t-shirt" style="background:linear-gradient(180deg,#a9dccf,#7cc4b4)"></div><h4>Youth Quill Girls' Apparel</h4><p>Youth Quill logos on clothes designed for girls and women</p><span class="ybtn">VIEW DETAILS</span></div>
  <div class="good" style="left:510px;top:3410px"><div class="im" role="img" aria-label="White raglan t-shirt with navy sleeves" style="background:linear-gradient(90deg,#1c2850 0 22%,#f4f4f4 22% 78%,#1c2850 78%)"></div><h4>Youth Quill Goodies</h4><p>Youth Quill logos on clothes designed for girls and women</p><span class="ybtn">VIEW DETAILS</span></div>
  <div class="good" style="left:740px;top:3410px"><div class="im" role="img" aria-label="Round pin button" style="width:120px;height:120px;border-radius:50%;background:radial-gradient(circle,#fff,#bbb)"></div><h4 style="margin-top:42px">Youth Quill Goodies</h4><p>Youth Quill logos on clothes designed for girls and women</p><span class="ybtn">VIEW DETAILS</span></div>
  <div class="arrows" style="left:585px;top:3670px">‹ ›</div>

  <div class="fcol" style="left:262px"><h5>About Us</h5><ul><li>About Us</li><li>Contact Us</li><li>Site Map</li><li>News &amp; Media</li><li>Link to Us</li><li>Our Partners</li><li>Our Programs</li><li>Our Books</li><li>Support/Donate</li><li>Celebrity Support</li><li>Celebrity Interviews</li><li>Subscribing Schools</li><li>Youth Quill FAQ</li><li>Privacy Policy</li><li>Terms of Service</li><li>Testimonials</li></ul></div>
  <div class="fcol" style="left:378px"><h5>Advertise</h5><ul><li>Advertise</li><li>Advertise in our Monthly Print Magazine</li><li>Advertise in our College Directory</li><li>Advertise Online</li><li>Sponsor a Page</li><li>Become a School Sponsor</li><li>Foundation Information</li><li>Advertising Information</li></ul></div>
  <div class="fcol" style="left:532px"><h5>Submit Work / Get Involved</h5><ul><li>Register &amp; Submit Your Work</li><li>Submit Your Book</li><li>Submission Guidelines</li><li>Video Submission Rules</li><li>Forum Guidelines</li><li>Writing Tips</li><li>Get Involved</li><li>Student Advisory Board</li><li>Subscribe to our Print Magazine</li><li>Win a Free Subscription</li></ul></div>
  <div class="fcol" style="left:692px"><h5>Contests</h5><ul><li>Cover Art Contest</li><li>Interview Contest</li><li>Nonfiction Contest</li><li>Poetry Contest</li><li>Educator of the Year Contest</li><li>Fiction Contest</li><li>Travel &amp; Culture Contest</li><li>Environment Contest</li><li>Community Service Award</li><li>Contest Winners</li></ul></div>
  <div class="fcol" style="left:822px"><h5>Other Youth Quill Goodies</h5><ul><li>Summer Program Links</li><li>College Links</li><li>YQ Summer Writing Program</li><li>Free Online Writing Classes</li><li>Youth Quill Book Previews</li><li>Youth Quill Weekly Newsletter</li><li>Ask for a Free Sample Issue</li><li>Youth Quill Store</li><li>Celebrity Interviews</li><li>Youth Quill Stories</li><li>Youth Quill Podcast</li><li>Video Series</li><li>Badge Program</li><li>Resources for Teens</li><li>Youth Quill Favorite Websites</li><li>Teacher Information</li><li>Library Services Board</li></ul></div>

  <div class="abs bottom">
    <div class="brand">Youth Quill</div>
    <div class="copy">© 2017 Company Name | All Right Reserved</div>
    <div class="soc">Connect With Us <i></i><i></i><i></i></div>
    <div class="up">↑ TOP</div>
  </div>

</div>
</body>
</html>
```